Stationery & Envelope Design

Executive Style looking stationery & envelope design.
Business Information:
Corla Home Partners
418 Maple Ridge Way, Fairbrook, OR 97321-5508
Phone: 916.555.0142
Fax: 916.555.0187

Industry/Entity Type

Business

```html
<!DOCTYPE html>
<html lang="en">
<head>
<meta charset="utf-8">
<title>Corla Home Partners – Envelope Set</title>
<link rel="stylesheet" href="https://fonts.googleapis.com/css2?family=Roboto:wght@400;700&display=swap">
<style>
  :root {
    --backdrop: #ebebeb;
    --paper: #f7f7f7;
    --paper-edge: #dcdcdc;
    --flap-shade: #efefef;
    --brand-navy: #2b4f8f;
    --text-grey: #6b6b6b;
    --deco-blue: #c3cfdd;
    --deco-sage: #d3d6c2;
  }
  * { box-sizing: border-box; margin: 0; padding: 0; }
  html, body {
    width: 1200px;
    height: 795px;
    overflow: hidden;
    background: var(--backdrop);
    font-family: "Roboto", Arial, sans-serif;
  }
  .stationery-set {
    position: relative;
    width: 1200px;
    height: 795px;
  }
  .envelope {
    position: absolute;
    top: 268px;
    width: 520px;
    height: 260px;
    background: var(--paper);
    border: 1px solid var(--paper-edge);
    box-shadow: 0 6px 14px rgba(0, 0, 0, 0.08);
    overflow: hidden;
  }
  .envelope--back { left: 50px; }
  .envelope--front { left: 630px; }

  .envelope__flap {
    position: absolute;
    inset: 0 0 auto 0;
    width: 520px;
    height: 130px;
  }
  .brand-name {
    position: absolute;
    display: flex;
    align-items: center;
    gap: 6px;
    color: var(--brand-navy);
    font-weight: 700;
    text-transform: uppercase;
    white-space: nowrap;
    letter-spacing: 0.02em;
  }
  .brand-name__dot {
    width: 9px;
    height: 9px;
    border-radius: 50%;
    background: var(--brand-navy);
  }
  .envelope--back .brand-name {
    top: 58px;
    left: 50%;
    transform: translateX(-50%);
    font-size: 12px;
  }
  .envelope--front .brand-name {
    top: 112px;
    left: 30px;
    font-size: 15px;
  }
  .decoration-area {
    position: absolute;
    right: 0;
    top: 0;
    width: 210px;
    height: 260px;
    background: linear-gradient(160deg, var(--deco-blue) 0%, var(--deco-sage) 70%, rgba(211, 214, 194, 0) 100%);
    opacity: 0.55;
  }
  .return-address {
    position: absolute;
    left: 30px;
    bottom: 24px;
    font-size: 9px;
    font-style: normal;
    line-height: 1.5;
    color: var(--text-grey);
    white-space: nowrap;
  }
  .return-address__name {
    color: var(--brand-navy);
    font-weight: 700;
  }
</style>
</head>
<body>
  <main class="stationery-set">
    <section class="envelope envelope--back" aria-label="Envelope back">
      <svg class="envelope__flap" viewBox="0 0 520 130" aria-hidden="true">
        <path d="M0 0 H520 V8 L500 118 Q498 128 486 128 H34 Q22 128 20 118 L0 8 Z"
              fill="var(--flap-shade)" stroke="var(--paper-edge)" stroke-width="1"/>
      </svg>
      <div class="brand-name"><span class="brand-name__dot"></span>Corla Home Partners</div>
    </section>

    <section class="envelope envelope--front" aria-label="Envelope front">
      <div class="decoration-area" role="img" aria-label="Faint brand decoration with house roofline, tree and sweeping curves"></div>
      <div class="brand-name"><span class="brand-name__dot"></span>Corla Home Partners</div>
      <address class="return-address">
        <span class="return-address__name">Corla Home Partners</span><br>
        418 Maple Ridge Way, Fairbrook, OR 97321-5508
      </address>
    </section>
  </main>
</body>
</html>
```